Business Card Design

We are a residential half way house for the addict ,the alcoholic and dual diagnosed in recovery.
i house both men and woman age 18+

Industry/Entity Type

Residential

```html
<!DOCTYPE html>
<html lang="en">
<head>
<meta charset="utf-8">
<title>Harbor Light Sober House – Business Card</title>
<link href="https://fonts.googleapis.com/css2?family=Ubuntu:wght@400;500;700&display=swap" rel="stylesheet">
<style>
  :root {
    --bg: #e6e4e0;
    --card: #ffffff;
    --card-shade: #f1f1f1;
    --red: #c0202e;
    --red-dark: #9e1722;
    --ink: #1b1b1b;
    --frame: #d9d9d9;
  }
  * { margin: 0; padding: 0; box-sizing: border-box; }
  html, body { width: 1200px; height: 818px; overflow: hidden; }
  body {
    background: var(--bg);
    font-family: "Ubuntu", sans-serif;
    display: flex; align-items: center; justify-content: center;
  }
  .card {
    position: relative;
    width: 1000px; height: 572px;
    background: linear-gradient(160deg, var(--card) 40%, var(--card-shade));
    box-shadow: 0 6px 20px rgba(0,0,0,.18);
    overflow: hidden;
  }
  .brand {
    position: absolute; left: 48px; top: 60px;
  }
  .brand-name {
    color: var(--red); font-weight: 700; font-size: 58px; line-height: 1;
  }
  .brand-sub {
    color: var(--ink); font-weight: 500; font-size: 32px; margin-top: 8px;
  }
  .brand-line {
    font-size: 22px; margin-top: 6px; color: var(--ink);
  }
  .brand-line .label { color: var(--red); font-weight: 500; margin-right: 8px; }
  .owner {
    position: absolute; right: 60px; top: 36px;
  }
  .owner-name { color: var(--red); font-weight: 700; font-size: 38px; }
  .owner-role { color: var(--ink); font-size: 26px; margin: 2px 0 8px; }
  .owner-phone {
    display: flex; align-items: center; gap: 10px;
    font-size: 24px; color: var(--ink); line-height: 1.2;
  }
  .owner-phone svg { width: 20px; height: 20px; }
  .gallery {
    position: absolute; left: 30px; right: 30px; top: 268px;
    display: grid; grid-template-columns: repeat(4, 1fr); gap: 14px;
  }
  .photo {
    height: 200px; padding: 8px; background: #fff;
    border: 1px solid var(--frame);
    box-shadow: 0 1px 3px rgba(0,0,0,.12);
  }
  .photo div { width: 100%; height: 100%; }
  .photo-party { background: linear-gradient(135deg, #f2c6a8, #c94a62 55%, #5a2030); }
  .photo-gym { background: linear-gradient(180deg, #bfbcb4, #8f8a78 55%, #6c6a52); }
  .photo-beach { background: linear-gradient(180deg, #f6e7b4, #f2a13a 55%, #1a1410); }
  .photo-dance { background: linear-gradient(135deg, #2a3a9a, #7a4a9a 50%, #c8402a); }
  .address-band {
    position: absolute; left: 0; right: 0; bottom: 0; height: 86px;
    background: linear-gradient(180deg, var(--red), var(--red-dark));
    color: #fff; font-size: 30px; font-weight: 500;
    display: flex; align-items: center; padding-left: 34px;
  }
</style>
</head>
<body>
  <article class="card">
    <section class="brand">
      <div class="brand-name">Harbor Light</div>
      <div class="brand-sub">Sober House Inc.</div>
      <div class="brand-line"><span class="label">fax</span>(555) 014-5536</div>
      <div class="brand-line"><span class="label">E mail:</span>mdelgado@harborlightmail.com</div>
    </section>

    <section class="owner">
      <div class="owner-name">Marisa Delgado</div>
      <div class="owner-role">Owner</div>
      <div class="owner-phone">
        <svg viewBox="0 0 20 20" aria-hidden="true"><rect width="20" height="20" fill="#1b1b1b"/><path d="M5 4c1 0 2 3 2 3l-1 1c1 2 3 4 5 5l1-1s3 1 3 2-1 2-2 2C8 16 4 12 4 6c0-1 0-2 1-2z" fill="#fff"/></svg>
        (555) 014-0305
      </div>
      <div class="owner-phone">
        <svg viewBox="0 0 20 20" aria-hidden="true"><rect width="20" height="20" fill="#1b1b1b"/><path d="M5 4c1 0 2 3 2 3l-1 1c1 2 3 4 5 5l1-1s3 1 3 2-1 2-2 2C8 16 4 12 4 6c0-1 0-2 1-2z" fill="#fff"/></svg>
        (555) 014-0306
      </div>
    </section>

    <section class="gallery">
      <figure class="photo"><div class="photo-party" role="img" aria-label="Photo of a young woman laughing at a celebration"></div></figure>
      <figure class="photo"><div class="photo-gym" role="img" aria-label="Photo of residents playing volleyball in a gym"></div></figure>
      <figure class="photo"><div class="photo-beach" role="img" aria-label="Photo of silhouetted group around a beach bonfire at sunset"></div></figure>
      <figure class="photo"><div class="photo-dance" role="img" aria-label="Photo of people dancing at an evening event"></div></figure>
    </section>

    <footer class="address-band">2480 Palm Grove Rd. Seabrook,Fla 33400</footer>
  </article>
</body>
</html>
```